female esthetician looking for an impact business card

I an an expert in skin care industry with high experience in NYC.I want my business card to look professional , an impact at first look. I do want a combination between white and gold . I believe the font will be great if is gold.. The Fonts are also important. MIRABELA COSTINA (SKIN CARE BOUTIQUE)

THIS SHOULD BE THE BUSINESS NAME, and should be placed on th eback of the card.
IN front m, the name MIRABELA COSTINA - ESTHETCIAN

BY APPOINTMENTS ONLY: 518.240.7136

Target Market(s)

HIGH END CLIENTELE

Contact Information for Business Card

iT WILL BE on a luxury paper. I neeed the wow feeling

Requirements
Should not have
• pictures

```html
<!DOCTYPE html>
<html lang="en">
<head>
<meta charset="utf-8">
<title>Mirabela Costina – Business Card</title>
<link rel="stylesheet" href="https://fonts.googleapis.com/css2?family=Cinzel:wght@400;600&family=Lato:wght@400&family=Josefin+Sans:wght@300&display=swap">
<style>
  :root {
    --backdrop: #8a8a8a;
    --card: #1c1c1c;
    --card-deep: #111111;
    --gold: #f2c417;
    --white: #ffffff;
    --ink-light: #f2f2f2;
    --rule: #777777;
  }
  * { margin: 0; padding: 0; box-sizing: border-box; }
  html, body { width: 1200px; height: 1200px; overflow: hidden; }
  body { background: var(--backdrop); position: relative; }

  .card {
    position: absolute;
    top: 310px;
    width: 366px;
    height: 594px;
    background: var(--card);
    box-shadow: 2px 3px 6px rgba(0,0,0,0.45);
    overflow: hidden;
    text-align: center;
  }
  .card--front { left: 234px; }
  .card--back { left: 628px; width: 370px; }

  .logo-mark-area {
    position: absolute;
    left: 136px; top: 107px;
    width: 95px; height: 76px;
    background: linear-gradient(135deg, #d9ad12, #f2c417);
    opacity: 0.85;
  }

  .brand-name {
    position: absolute; left: 0; right: 0;
    font-family: "Cinzel", serif;
    font-weight: 400;
    color: var(--gold);
    letter-spacing: 1px;
    white-space: nowrap;
  }
  .card--front .brand-name { top: 196px; font-size: 27px; }
  .card--back .brand-name { top: 290px; font-size: 28px; }

  .brand-tagline {
    position: absolute; left: 0; right: 0;
    font-family: "Josefin Sans", sans-serif;
    font-weight: 300;
    font-size: 11px;
    letter-spacing: 5px;
    color: var(--white);
    white-space: nowrap;
  }
  .card--front .brand-tagline { top: 234px; }
  .card--back .brand-tagline { top: 332px; }

  .person-name {
    position: absolute; left: 0; right: 0; top: 330px;
    font-family: "Cinzel", serif;
    font-weight: 600;
    font-size: 25px;
    color: var(--gold);
    white-space: nowrap;
  }
  .person-role {
    position: absolute; left: 0; right: 0; top: 359px;
    font-family: "Lato", sans-serif;
    font-size: 17px;
    color: var(--white);
  }
  .contact-icons { position: absolute; left: 0; top: 394px; }

  .contact-list, .address {
    position: absolute; left: 0; right: 0;
    font-family: "Lato", sans-serif;
    font-size: 17px;
    line-height: 22px;
    color: var(--ink-light);
    list-style: none;
    white-space: nowrap;
  }
  .contact-list { top: 431px; }
  .appointments { color: var(--gold); }
  .divider {
    position: absolute; top: 506px; left: 88px;
    width: 194px; height: 1px; background: var(--rule);
  }
  .address { top: 517px; font-style: normal; }

  .pattern-area {
    position: absolute; inset: 0;
    background:
      radial-gradient(circle at 20% 15%, #0d0d0d 0, transparent 45%),
      radial-gradient(circle at 90% 45%, #0d0d0d 0, transparent 40%),
      radial-gradient(circle at 25% 85%, #0d0d0d 0, transparent 45%),
      linear-gradient(180deg, var(--card) 0%, var(--card-deep) 100%);
  }
</style>
</head>
<body>

<section class="card card--front">
  <div class="logo-mark-area" role="img" aria-label="Gold ornamental logo frame"></div>
  <h1 class="brand-name">MIRABELA COSTINA</h1>
  <p class="brand-tagline">SKIN CARE BOUTIQUE</p>

  <h2 class="person-name">MIRABELA COSTINA</h2>
  <p class="person-role">Esthetician</p>

  <svg class="contact-icons" width="366" height="30" viewBox="0 0 366 30" aria-hidden="true">
    <line x1="87" y1="14" x2="142" y2="14" stroke="var(--rule)" stroke-width="1"/>
    <line x1="223" y1="14" x2="277" y2="14" stroke="var(--rule)" stroke-width="1"/>
    <circle cx="154" cy="14" r="12" fill="var(--gold)"/>
    <path d="M148 11 q6 -5 12 0 l-1.5 2 h-2 l-0.5 -1.5 h-4 l-0.5 1.5 h-2 z M149 14 h10 v5 h-10 z" fill="var(--card)"/>
    <circle cx="182" cy="14" r="12" fill="var(--gold)"/>
    <rect x="175" y="9" width="14" height="10" fill="var(--card)"/>
    <path d="M175.5 9.5 L182 15 L188.5 9.5" stroke="var(--gold)" stroke-width="1.3" fill="none"/>
    <circle cx="209" cy="14" r="12" fill="var(--gold)"/>
    <circle cx="209" cy="14" r="6.5" fill="var(--card)"/>
    <path d="M206 10 q3 1 2 4 q-2 1 -1 4 M211 9 q1 2 3 2 M212 15 q1 2 2 1" stroke="var(--gold)" stroke-width="1.4" fill="none"/>
  </svg>

  <ul class="contact-list">
    <li class="appointments">By Appointments Only: 518.240.7136</li>
    <li>hello@mirabelacostina.com</li>
    <li>www.mirabelacostina.com</li>
  </ul>
  <div class="divider"></div>
  <address class="address">
    57 Lexington Avenue, Suite 9,<br>
    New York, NY 10022
  </address>
</section>

<section class="card card--back">
  <div class="pattern-area" role="img" aria-label="Dark tone-on-tone flourish pattern"></div>
  <h1 class="brand-name">MIRABELA COSTINA</h1>
  <p class="brand-tagline">SKIN CARE BOUTIQUE</p>
</section>

</body>
</html>
```